Carpet cleaning company focused on high quality needs business cards

We are a growing company that just merged with another company and need to design a new business card. We do both residential as well as commercial cleaning. We do carpet, tile & grout, upholstery, hard floors, and stain & pet odor removal. We treat our customers like family and strive to achieve outstanding results with every job.

```html
<!DOCTYPE html>
<html lang="en">
<head>
<meta charset="utf-8">
<title>Maple Grove Floor Care – Business Card</title>
<link rel="stylesheet" href="https://fonts.googleapis.com/css2?family=Open+Sans:wght@600;700;800&family=Montserrat:wght@700&display=swap">
<style>
  :root {
    --bg: #9a9a9a;
    --paper: #ffffff;
    --red: #ef4641;
    --ink: #231f20;
    --service-blue: #3c5a9a;
    --mascot-blue: #2f7fc1;
    --mascot-tan: #c79a5a;
    --white: #ffffff;
  }
  * { box-sizing: border-box; margin: 0; padding: 0; }
  html, body {
    width: 1200px; height: 1200px; overflow: hidden;
    background: var(--bg);
    font-family: "Open Sans", Arial, sans-serif;
  }
  .card {
    position: absolute; left: 200px;
    width: 797px; height: 465px;
    background: var(--paper);
    overflow: hidden;
  }
  .card--front { top: 89px; }
  .card--back { top: 624px; }

  /* Front */
  .front-band { position: absolute; inset: 0; }
  .brand-name {
    color: var(--ink); font-weight: 800; line-height: 1.05;
    letter-spacing: -0.5px;
  }
  .tagline {
    color: var(--red); font-weight: 700; text-transform: uppercase;
    letter-spacing: 0.6px;
  }
  .front-brand { position: absolute; left: 50px; top: 128px; width: 360px; }
  .front-brand .brand-name { font-size: 52px; }
  .front-brand .tagline { font-size: 15px; margin-top: 12px; }
  .mascot-front { position: absolute; left: 424px; top: 0; width: 340px; height: 465px; }

  /* Back */
  .back-brand { position: absolute; left: 50px; top: 22px; }
  .back-brand__row { display: flex; align-items: flex-end; gap: 10px; }
  .mascot-back { width: 96px; height: 110px; display: block; }
  .back-brand .brand-name { font-size: 21px; padding-bottom: 4px; }
  .back-brand .tagline { font-size: 15px; margin-top: 6px; }

  .person { position: absolute; left: 474px; top: 82px; }
  .person__name {
    font-family: "Montserrat", Arial, sans-serif; font-weight: 700;
    font-size: 33px; color: #111; letter-spacing: -0.3px;
  }
  .person__role {
    color: var(--red); font-size: 16px; font-weight: 600;
    letter-spacing: 3.5px; text-transform: uppercase; margin-top: 2px;
  }

  .services {
    position: absolute; top: 202px; list-style: none;
    color: var(--service-blue); font-size: 26px; font-weight: 600;
  }
  .services li { height: 44px; line-height: 40px; }
  .services li::before { content: "•"; margin-right: 8px; }
  .services--left { left: 46px; }
  .services--right { left: 471px; }

  .contact-bar {
    position: absolute; left: 0; right: 0; bottom: 0; height: 94px;
    background: var(--red); color: var(--white);
    display: flex; justify-content: space-between; align-items: center;
    padding: 0 53px 0 50px; font-size: 21px;
  }
  .contact-col { display: flex; flex-direction: column; gap: 1px; }
  .contact-col--right { align-items: flex-end; }
  .contact-item { display: flex; align-items: center; gap: 9px; line-height: 27px; }
  .icon { width: 18px; height: 18px; flex: none; }
  .social-dot { width: 14px; height: 14px; border-radius: 50%; background: var(--white); flex: none; }
</style>
</head>
<body>

<section class="card card--front">
  <svg class="front-band" viewBox="0 0 797 465" preserveAspectRatio="none" aria-hidden="true">
    <polygon points="0,429 797,226 797,465 0,465" fill="var(--red)"/>
  </svg>
  <div class="front-brand">
    <h1 class="brand-name">Maple Grove Floor Care</h1>
    <p class="tagline">Residential &amp; Commercial</p>
  </div>
  <svg class="mascot-front" viewBox="0 0 340 465" role="img" aria-label="Illustrated mascot: cheerful cleaner in cap and blue shirt raising a steam cleaning wand">
    <defs>
      <linearGradient id="mascotFront" x1="0" y1="0" x2="0" y2="1">
        <stop offset="0" stop-color="var(--mascot-blue)" stop-opacity="0.35"/>
        <stop offset="0.55" stop-color="var(--mascot-blue)" stop-opacity="0.75"/>
        <stop offset="1" stop-color="var(--mascot-tan)" stop-opacity="0.85"/>
      </linearGradient>
    </defs>
    <rect x="20" y="0" width="310" height="465" rx="18" fill="url(#mascotFront)"/>
  </svg>
</section>

<section class="card card--back">
  <div class="back-brand">
    <div class="back-brand__row">
      <svg class="mascot-back" viewBox="0 0 96 110" role="img" aria-label="Small mascot of the cleaner with steam wand">
        <defs>
          <linearGradient id="mascotBack" x1="0" y1="0" x2="0" y2="1">
            <stop offset="0" stop-color="var(--mascot-blue)" stop-opacity="0.4"/>
            <stop offset="1" stop-color="var(--red)" stop-opacity="0.85"/>
          </linearGradient>
        </defs>
        <rect x="0" y="0" width="96" height="110" rx="8" fill="url(#mascotBack)"/>
      </svg>
      <p class="brand-name">Maple Grove<br>Floor Care</p>
    </div>
    <p class="tagline">Residential &amp; Commercial</p>
  </div>

  <div class="person">
    <p class="person__name">Name Surname</p>
    <p class="person__role">Position</p>
  </div>

  <ul class="services services--left">
    <li>Carpet Cleaning</li>
    <li>Tile &amp; Grout Cleaning</li>
    <li>Upholstery Cleaning</li>
  </ul>
  <ul class="services services--right">
    <li>Hard floors</li>
    <li>Pet Odor Removal</li>
    <li>Air Duct Cleaning</li>
  </ul>

  <footer class="contact-bar">
    <div class="contact-col">
      <p class="contact-item">
        <svg class="icon" viewBox="0 0 24 24" aria-hidden="true"><path fill="var(--white)" d="M6.6 10.8a15.1 15.1 0 0 0 6.6 6.6l2.2-2.2a1 1 0 0 1 1-.25 11.4 11.4 0 0 0 3.6.57 1 1 0 0 1 1 1V20a1 1 0 0 1-1 1A17 17 0 0 1 3 4a1 1 0 0 1 1-1h3.5a1 1 0 0 1 1 1c0 1.25.2 2.45.57 3.57a1 1 0 0 1-.25 1z"/></svg>
        (555) 014-2290
      </p>
      <p class="contact-item">
        <svg class="icon" viewBox="0 0 24 24" aria-hidden="true"><rect x="2.5" y="5" width="19" height="14" rx="1.5" fill="none" stroke="var(--white)" stroke-width="1.8"/><path d="M3 6l9 7 9-7" fill="none" stroke="var(--white)" stroke-width="1.8"/></svg>
        hello@maplegrovecare.com
      </p>
    </div>
    <div class="contact-col contact-col--right">
      <p class="contact-item">maplegrovecare <span class="social-dot" aria-hidden="true"></span></p>
      <p class="contact-item">maplegrovecare.com
        <svg class="icon" viewBox="0 0 24 24" aria-hidden="true"><g fill="none" stroke="var(--white)" stroke-width="1.5"><circle cx="12" cy="12" r="9"/><ellipse cx="12" cy="12" rx="4" ry="9"/><path d="M3 12h18M5 7.5h14M5 16.5h14"/></g></svg>
      </p>
    </div>
  </footer>
</section>

</body>
</html>
```